The 22 Rules and Traps of House Lending or the 22 things that will derail your transaction and how to prevent them.

I am looking to do a series of 4 to 5 e-books that should have a consistent format and theme

The first of these should be entitled, "The 22 Rules and Traps of House Lending" That is similar in style to the attached e-book.
The attached e-book is pretty much the style that I am looking for, The same format can be followed. I have attached a black and white head shot image for the head shot areas that appears on page two of the attached e-book. I have also attached my company logo.
Please feel free to use the same or similar colors in my logo for the lay-out of the e-book. However please do not feel limited to those colors. - Feel free to use your imagination.

The content can be found here.

http://www.fredtheloanfox.example/loan-advice.php

For the final “About” page of the e-book - Please entitle it… About Fred the Loan Fox.
The content for the last page can be found in the attached document - Owen Thistlewood bio2

The first page is where the creativity come in

Requirements
Must have
• Note that this project is for one e-book - However, once the designer and format is chosen the remainder of the projects will be launched

```html
<!DOCTYPE html>
<html lang="en">
<head>
<meta charset="utf-8">
<title>The 22 Rules and Traps of House Lending – Page 5</title>
<link rel="stylesheet" href="https://fonts.googleapis.com/css2?family=Montserrat:wght@600;700;800&family=Open+Sans:ital,wght@0,400;0,700;1,700&display=swap">
<style>
  :root{
    --navy:#1d2a5c;
    --red:#d2232a;
    --blue:#2d62b3;
    --body:#4a4a4a;
    --rule:#c9ccd6;
    --page:#ffffff;
  }
  *{box-sizing:border-box;margin:0;padding:0}
  html,body{width:900px;height:1200px;overflow:hidden;background:var(--page)}
  .page{position:relative;width:900px;height:1200px;background:var(--page);font-family:"Open Sans",Arial,sans-serif;color:var(--body);padding:28px 40px 0 0}
  .rule-item{position:relative}
  .item-08{margin-top:96px}
  .item-09{margin-top:34px}
  .item-header{display:flex;align-items:center;gap:18px;margin-left:16px}
  .item-number{flex:0 0 72px;height:72px;border-radius:50%;background:var(--navy);color:#fff;
    font-family:"Montserrat",Arial,sans-serif;font-weight:800;font-size:30px;display:flex;align-items:center;justify-content:center}
  .item-title{font-family:"Montserrat",Arial,sans-serif;font-weight:600;font-size:25px;line-height:1.22;color:var(--navy)}
  .item-title .dont{color:var(--red);font-weight:700}
  .item-body{margin:14px 0 0 60px}
  .item-body p{font-size:14.6px;line-height:1.5;margin-bottom:12px;text-align:justify}
  .item-body p.highlight{font-weight:700;color:var(--blue);font-size:16.4px;line-height:1.45}
  .footer{position:absolute;left:30px;right:30px;top:1112px;height:60px;border-top:2px solid var(--rule);display:flex;align-items:center;justify-content:space-between;padding-top:8px}
  .brand{display:flex;align-items:center;gap:8px;font-family:"Montserrat",Arial,sans-serif;font-weight:800;font-size:13px;color:var(--navy);text-transform:uppercase}
  .brand-mark{width:18px;height:18px;background:var(--red)}
  .footer-title{font-family:"Montserrat",Arial,sans-serif;font-weight:700;font-size:12px;color:var(--navy);text-transform:uppercase;letter-spacing:.4px}
  .footer-title .accent{color:var(--red)}
  .footer-meta{display:flex;align-items:center;gap:22px;font-family:"Montserrat",Arial,sans-serif;font-weight:700;font-size:11px;color:var(--navy);text-transform:uppercase}
  .page-number{font-size:15px}
</style>
</head>
<body>
<main class="page">

  <section class="rule-item item-07">
    <div class="item-header">
      <div class="item-number">07</div>
      <h2 class="item-title"><span class="dont">Don’t</span> co-sign for any auto loans or other debt any during the underwriting pro-cess.</h2>
    </div>
    <div class="item-body">
      <p>Some borrowers are under the mistaken assumption that co-signing or endors-ing a note will not affect their debt load, and that type of new debt will not affect their credit or their ability to obtain a mortgage. Any debt for which a borrower co-signs will affect their credit and their ability to obtain a mortgage.</p>
      <p>Although someone else may have promised to make the payments on the new debt, you are ultimately responsible for the other party’s payments if they cannot make them. In the eyes of the lender and the underwriter you and the borrower are equally responsible for the payments.</p>
      <p class="highlight">Also, when you co-sign for another person and they obtain new credit, it’s an-other underwriting double-whammy. Not only have you incurred an unneces-sary credit inquiry on your credit report, you have increased your debt load which can in some cases adversely effect your debt-to-income ratio.</p>
    </div>
  </section>

  <section class="rule-item item-08">
    <div class="item-header">
      <div class="item-number">08</div>
      <h2 class="item-title"><span class="dont">Don’t</span> list your property for sale while in the process of refinancing.</h2>
    </div>
    <div class="item-body">
      <p>When a lender provides funds for a refinance, the lender expects that the new loan will remain in place for a reasonable period of time. While there is no exact length that defines this “reasonable period of time,” most lenders like their loans to remain active for at least three months and some up to six months.</p>
      <p class="highlight">If a lender notices that the property they are refinancing is listed for sale during the underwriting process, they will decline the loan because the likelihood of the loan remaining active for three to six months is unlikely.</p>
    </div>
  </section>

  <section class="rule-item item-09">
    <div class="item-header">
      <div class="item-number">09</div>
      <h2 class="item-title">Do provide all requested paperwork in a timely manner.</h2>
    </div>
    <div class="item-body">
      <p>Not all borrowers are well organized and some have trouble finding all the required paperwork. While there is no exact definition for “timely,” it is in everyone’s best interest to act responsibly when gathering the necessary paperwork in order to quickly complete the underwriting of a loan, especially when other buyers and sellers are depending upon a timely closing.</p>
      <p class="highlight">The longer it takes to gather paperwork to satisfy the lender’s conditions, the longer it takes to successfully close your loan. If you have any difficulty gather-ing paperwork or documentation, please inform your mortgage professional quickly so an alternate strategy can be devised to ensure a successful closing.</p>
    </div>
  </section>

  <footer class="footer">
    <div class="brand"><span class="brand-mark"></span>Harbor Lane Lending</div>
    <div class="footer-title">The 22 <span class="accent">Rules and Traps</span> of House Lending</div>
    <div class="footer-meta"><span>License NMLS 000000</span><span class="page-number">5</span></div>
  </footer>

</main>
</body>
</html>
```